Business card design for my company.
I would like the card's background colour to be black. You can also see our web site to get an idea of our brand. https://www.tmwhomecrafting.com.au/
- Name
- Email

```html
<!DOCTYPE html>
<html lang="en">
<head>
<meta charset="utf-8">
<title>TMW Home Crafting – Business Card</title>
<link rel="stylesheet" href="https://fonts.googleapis.com/css2?family=Roboto:wght@400;500;700&display=swap">
<style>
  :root {
    --stage: #2b2b2b;
    --card-black: #1c1c1c;
    --ink: #111111;
    --green: #16a04a;
    --grey-line: #9a9a9a;
    --paper: #f7f7f7;
    --muted: #555555;
    --back-mark: #4a4a4a;
    --back-text: #e6e6e6;
  }
  * { box-sizing: border-box; margin: 0; padding: 0; }
  html, body {
    width: 1200px; height: 852px; overflow: hidden;
    background: var(--stage);
    font-family: "Roboto", Arial, sans-serif;
  }
  .stage { position: relative; width: 1200px; height: 852px; }

  .card {
    position: absolute;
    width: 560px; height: 320px;
    border-radius: 22px;
    overflow: hidden;
  }

  /* Back side */
  .card-back {
    left: 60px; top: 96px;
    background: var(--card-black);
    border-bottom: 8px solid var(--green);
  }
  .card-back .brand {
    position: absolute; left: 0; right: 0; top: 120px;
    text-align: center;
    font-weight: 700; font-size: 34px; letter-spacing: 2px;
    color: var(--back-mark);
  }
  .card-back .web {
    position: absolute; right: 40px; bottom: 26px;
    font-size: 15px; color: var(--back-text);
  }

  /* Front side */
  .card-front {
    left: 580px; top: 436px;
    background: var(--paper);
  }
  .side-band {
    position: absolute; left: 0; top: 0; bottom: 0; width: 36px;
    background: linear-gradient(to bottom, var(--green) 0 58%, var(--ink) 58% 100%);
  }
  .side-line {
    position: absolute; left: 46px; top: 0; bottom: 0; width: 6px;
    background: var(--grey-line);
  }
  .brand-front {
    position: absolute; left: 84px; top: 46px;
    display: flex; align-items: center; gap: 12px;
    font-weight: 700; font-size: 30px; letter-spacing: 1px;
    color: var(--ink);
    white-space: nowrap;
  }
  .brand-front .brand-square {
    width: 18px; height: 18px; background: var(--green); flex: none;
  }
  .person { position: absolute; left: 84px; top: 148px; }
  .person .name { font-size: 24px; font-weight: 500; color: var(--green); }
  .person .role { font-size: 14px; color: var(--muted); margin-top: 2px; }

  .contacts {
    position: absolute; list-style: none;
    font-size: 14px; color: var(--muted);
    white-space: nowrap;
  }
  .contacts li { display: flex; align-items: center; gap: 10px; margin-bottom: 8px; }
  .contacts svg { width: 14px; height: 14px; fill: var(--green); flex: none; }
  .contacts-left { left: 84px; top: 240px; }
  .contacts-right { left: 300px; top: 150px; }
</style>
</head>
<body>
<main class="stage">

  <section class="card card-back" aria-label="Business card back">
    <div class="brand">TMW HOME CRAFTING</div>
    <div class="web">www.tmwhomecrafting.com.au</div>
  </section>

  <section class="card card-front" aria-label="Business card front">
    <div class="side-band"></div>
    <div class="side-line"></div>

    <div class="brand-front">
      <span class="brand-square"></span>
      <span>TMW HOME CRAFTING</span>
    </div>

    <div class="person">
      <div class="name">Liam Harper</div>
      <div class="role">General Manager</div>
    </div>

    <ul class="contacts contacts-right">
      <li>
        <svg viewBox="0 0 16 16"><path d="M1 3h14v10H1z M1 3l7 6 7-6" fill="none" stroke="#16a04a" stroke-width="1.6"/></svg>
        info@tmwhomecrafting.com.au
      </li>
      <li>
        <svg viewBox="0 0 16 16"><circle cx="8" cy="8" r="7"/><path d="M1 8h14M8 1c3 3 3 11 0 14M8 1c-3 3-3 11 0 14" stroke="#f7f7f7" stroke-width="1" fill="none"/></svg>
        www.tmwhomecrafting.com.au
      </li>
    </ul>

    <ul class="contacts contacts-left">
      <li>
        <svg viewBox="0 0 16 16"><path d="M4 1l3 3-2 2c1 2 3 4 5 5l2-2 3 3-2 3C7 15 1 9 1 3z"/></svg>
        0400 555 172
      </li>
      <li>
        <svg viewBox="0 0 16 16"><path d="M8 1a5 5 0 0 1 5 5c0 4-5 9-5 9S3 10 3 6a5 5 0 0 1 5-5z"/><circle cx="8" cy="6" r="2" fill="#f7f7f7"/></svg>
        Larkfield, Eastvale, Australia
      </li>
    </ul>
  </section>

</main>
</body>
</html>
```